Electrician Letterhead Design MVR

We need some letterhead for our bills and other papers.
Customer address is on the right side (Swiss format)
A4 format

Design should also be applicable on Cards

Target Market(s)

Private Customers, Small Business

Industry/Entity Type

Electrician

Other font styles liked:
• incised 901

Colors
00AB8E
00BBA5
67D7C9
C6EFE9
E9F9F6

```html
<!DOCTYPE html>
<html lang="de">
<head>
<meta charset="utf-8">
<title>MVR Letterhead</title>
<link href="https://fonts.googleapis.com/css2?family=Arvo:wght@400;700&display=swap" rel="stylesheet">
<style>
  :root {
    --backdrop: #dadada;
    --paper: #ffffff;
    --brand-teal: #0aa190;
    --band-dark: #2f2f2f;
    --watermark: #ebebeb;
    --text-light: #ffffff;
  }
  html, body {
    margin: 0;
    padding: 0;
    width: 1200px;
    height: 947px;
    overflow: hidden;
    background: var(--backdrop);
  }
  .canvas {
    position: relative;
    width: 1200px;
    height: 947px;
    background: var(--backdrop);
    font-family: "Arvo", serif;
  }
  .letterhead {
    position: absolute;
    left: 364px;
    top: 179px;
    width: 472px;
    height: 605px;
    background: var(--paper);
    overflow: hidden;
  }
  .brand-name {
    position: absolute;
    right: 36px;
    top: 22px;
    margin: 0;
    font-family: "Arvo", serif;
    font-weight: 700;
    font-size: 46px;
    line-height: 1;
    letter-spacing: 1px;
    color: var(--brand-teal);
  }
  .brand-watermark {
    position: absolute;
    left: 230px;
    top: 330px;
    transform: translate(-50%, -50%) rotate(-45deg);
    font-family: "Arvo", serif;
    font-weight: 700;
    font-size: 170px;
    line-height: 1;
    color: var(--watermark);
    white-space: nowrap;
    user-select: none;
  }
  .footer-graphic {
    position: absolute;
    left: 0;
    top: 0;
    width: 472px;
    height: 605px;
  }
  .footer-graphic .teal { fill: var(--brand-teal); }
  .footer-graphic .divider { fill: var(--paper); }
  .footer-graphic .dark { fill: var(--band-dark); }
  .address-line {
    position: absolute;
    left: 47px;
    top: 550px;
    font-size: 10px;
    line-height: 16px;
    color: var(--text-light);
  }
  .contact-line {
    position: absolute;
    left: 44px;
    top: 583px;
    font-size: 8.5px;
    line-height: 14px;
    color: var(--text-light);
    white-space: nowrap;
  }
  .contact-line .label {
    color: var(--brand-teal);
    font-weight: 700;
  }
  .contact-line .sep { margin: 0 3px; }
</style>
</head>
<body>
<div class="canvas">
  <div class="letterhead">
    <div class="brand-watermark" aria-hidden="true">MVR</div>
    <h1 class="brand-name">MVR</h1>

    <svg class="footer-graphic" viewBox="0 0 472 605" aria-hidden="true">
      <polygon class="teal" points="0,545 431,545 388,504 418,504 472,557 424,605 0,605"/>
      <polygon class="divider" points="0,569 431,569 395,605 0,605"/>
      <polygon class="dark" points="0,572 427,572 392,605 0,605"/>
    </svg>

    <div class="address-line">Your Address line here, Country Code 0123456</div>
    <div class="contact-line">
      <span class="label">P:</span> 044-123 456 789<span class="sep">|</span>
      <span class="label">E:</span> info@webname.com<span class="sep">|</span>
      <span class="label">W:</span> www.websitename.com
    </div>
  </div>
</div>
</body>
</html>
```